Quote Cards With KB May 2025 for Instagram

I would like to put these quotes over one of the pictures attached; Instagram (new size: 4:5 (1080 x 1350 pixels) One Quote per picture, and I want the quote to be bold or easy to read as well. I provided a few reference graphics that I really like as examples below. In very small letters at the bottom add @KBHarlowOnline

All of the pictures are attached; you can pick any photo and add one quote to it; but no stock photography

```html
<!DOCTYPE html>
<html lang="en">
<head>
<meta charset="utf-8">
<title>Quote Cards – KB Harlow</title>
<link href="https://fonts.googleapis.com/css2?family=Outfit:wght@400;500;600;700&display=swap" rel="stylesheet">
<style>
  :root {
    --page-bg: #d4d4d4;
    --magenta: #d10068;
    --hot-pink: #ff3399;
    --soft-pink: #ff8cc6;
    --blush: #ffb3da;
    --light-pink: #f9c8e3;
    --ink: #1c1c1c;
    --white: #ffffff;
    --night: #1e1a4a;
  }
  * { margin: 0; padding: 0; box-sizing: border-box; }
  html, body { width: 1200px; height: 1005px; overflow: hidden; }
  body {
    background: var(--page-bg);
    font-family: "Outfit", sans-serif;
    position: relative;
  }
  .card {
    position: absolute;
    width: 340px;
    height: 425px;
    overflow: hidden;
    box-shadow: 0 2px 6px rgba(0,0,0,0.12);
  }
  .row-top { top: 56px; }
  .row-bottom { top: 525px; }
  .col-1 { left: 47px; }
  .col-2 { left: 430px; }
  .col-3 { left: 813px; }

  .photo { position: absolute; inset: 0; }
  .handle {
    position: absolute;
    left: 0; right: 0;
    text-align: center;
    font-size: 8px;
    font-weight: 400;
    color: var(--white);
  }
  .block { position: absolute; left: 0; right: 0; text-align: center; }

  /* Card 1 */
  .portrait-photo {
    background: linear-gradient(180deg, #b9d8ef 0%, #9fb59a 45%, #4e6e3c 100%);
  }
  .intro-panel {
    position: absolute;
    left: 165px; top: 0; width: 167px; height: 425px;
    background: linear-gradient(180deg, rgba(255,255,255,1) 0%, rgba(255,255,255,0.97) 55%, rgba(255,255,255,0.5) 78%, rgba(255,255,255,0) 95%);
  }
  .intro-panel .block { color: #2a2a2a; }
  .intro-headline { top: 74px; font-size: 28px; font-weight: 600; line-height: 31px; color: var(--hot-pink) !important; }
  .intro-body { top: 150px; font-size: 21px; font-weight: 500; line-height: 25px; }
  .intro-cta { top: 236px; font-size: 15px; font-weight: 400; }
  .intro-keyword { top: 262px; font-size: 25px; font-weight: 500; color: #111 !important; }
  .intro-note { top: 298px; font-size: 15px; line-height: 19px; }
  .handle-pill {
    position: absolute;
    left: 97px; top: 396px; width: 146px; height: 20px;
    border-radius: 10px;
    background: var(--white);
    color: var(--ink);
    font-size: 8px;
    display: flex; align-items: center; justify-content: center;
  }

  /* Card 2 */
  .courtside-photo {
    background: linear-gradient(160deg, #3b4a8c 0%, #7a6a72 40%, #2b2b3a 100%);
    height: 300px;
  }
  .wave { position: absolute; left: 0; top: 0; }
  .avatar {
    position: absolute;
    left: 191px; top: 189px; width: 98px; height: 98px;
    border-radius: 50%;
    border: 3px solid var(--white);
    background: linear-gradient(180deg, #8a7a70 0%, #3a302c 100%);
  }
  .belly-lead { top: 298px; font-size: 16px; font-weight: 500; color: var(--white); }
  .belly-title { top: 318px; font-size: 32px; font-weight: 700; color: var(--white); }
  .belly-sub { top: 355px; font-size: 16px; font-weight: 300; line-height: 19px; color: var(--white); }

  /* Card 3 */
  .stage-photo {
    background:
      radial-gradient(ellipse at 58% 60%, rgba(232,40,160,0.7) 0%, rgba(232,40,160,0) 45%),
      radial-gradient(ellipse at 85% 10%, rgba(220,150,60,0.6) 0%, rgba(220,150,60,0) 40%),
      linear-gradient(180deg, #3b2f6e 0%, var(--night) 60%, #12112b 100%);
  }
  .stage-title { top: 98px; font-size: 41px; font-weight: 700; line-height: 50px; color: var(--white); }
  .stage-body { top: 208px; font-size: 27px; font-weight: 500; line-height: 31px; color: var(--white); }

  /* Card 4 */
  .card-magenta { background: var(--magenta); }
  .tummy-question { top: 72px; font-size: 25px; font-weight: 400; line-height: 28px; color: var(--white); }
  .tummy-cta { top: 146px; font-size: 37px; font-weight: 700; line-height: 41px; color: var(--white); }
  .tummy-cta .keyword { color: var(--blush); font-size: 40px; }

  /* Card 5 */
  .card-gradient { background: linear-gradient(180deg, var(--soft-pink) 0%, var(--hot-pink) 45%, var(--hot-pink) 100%); }
  .plan-lead { top: 82px; font-size: 50px; font-weight: 700; color: var(--white); line-height: 56px; }
  .plan-body { top: 134px; font-size: 32px; font-weight: 600; line-height: 34.5px; color: var(--white); }

  /* Card 6 */
  .card-light { background: radial-gradient(ellipse at 50% 45%, #ffd6ec 0%, var(--light-pink) 45%, var(--blush) 100%); }
  .secret-body { top: 48px; font-size: 32px; font-weight: 600; line-height: 34.5px; color: var(--ink); }
  .secret-cta { top: 238px; font-size: 30px; font-weight: 400; color: var(--ink); }
  .secret-keyword { top: 270px; font-size: 46px; font-weight: 700; color: var(--magenta); }
  .secret-tail { top: 320px; font-size: 29px; font-weight: 400; color: var(--ink); }
  .card-light .handle { color: var(--ink); }
</style>
</head>
<body>

  <section class="card row-top col-1">
    <div class="photo portrait-photo" role="img" aria-label="Photo of KB standing outdoors in a black outfit against greenery and hills"></div>
    <div class="intro-panel">
      <p class="block intro-headline">Your belly<br>isn’t fat...</p>
      <p class="block intro-body">it’s hormonal.<br>And here’s<br>how to fix it.</p>
      <p class="block intro-cta">Comment</p>
      <p class="block intro-keyword">HORMONES</p>
      <p class="block intro-note">if nothing is<br>working.</p>
    </div>
    <div class="handle-pill">@KBHarlowOnline</div>
  </section>

  <section class="card row-top col-2" style="background: var(--hot-pink);">
    <div class="photo courtside-photo" role="img" aria-label="Photo of KB courtside at a basketball game holding a ball, with fans around"></div>
    <svg class="wave" width="340" height="425" viewBox="0 0 340 425" aria-hidden="true">
      <path d="M0 253 C 20 280, 50 295, 85 290 C 150 280, 210 230, 270 225 C 300 222, 325 240, 340 250 L340 425 L0 425 Z" fill="var(--hot-pink)"/>
    </svg>
    <div class="avatar" role="img" aria-label="Small round portrait of KB"></div>
    <p class="block belly-lead">Tired. Moody.</p>
    <p class="block belly-title">Stubborn Belly Fat.</p>
    <p class="block belly-sub">Your hormonesare screaming<br>for help! Let’s fix that.</p>
    <p class="handle" style="top: 406px;">@KBHarlowOnline</p>
  </section>

  <section class="card row-top col-3">
    <div class="photo stage-photo" role="img" aria-label="Photo of KB on stage in a pink gown under bright lights"></div>
    <p class="block stage-title">That stubborn<br>weight?</p>
    <p class="block stage-body">It’s not your fault.<br>Your hormones are<br>to blame and<br>you’re not alone;<br>But there is a fix.</p>
    <p class="handle" style="top: 403px;">@KBHarlowOnline</p>
  </section>

  <section class="card row-bottom col-1 card-magenta">
    <p class="block tummy-question">Flat tummy in your 40s?<br>It’s still possible!</p>
    <p class="block tummy-cta">Comment<br><span class="keyword">BYE BELLY</span><br>to get the 10<br>secrets to a<br>flatter tummy</p>
    <p class="handle" style="top: 403px;">@KBHarlowOnline</p>
  </section>

  <section class="card row-bottom col-2 card-gradient">
    <p class="block plan-lead">This 90-day</p>
    <p class="block plan-body">plan helped<br>women over 40 slim<br>down, get a tiny<br>waist and feel<br>sexy again.<br>You’re next.</p>
    <p class="handle" style="top: 403px;">@KBHarlowOnline</p>
  </section>

  <section class="card row-bottom col-3 card-light">
    <p class="block secret-body">This is the secret<br>women over 40<br>are using to get<br>snatched; without<br>starving.</p>
    <p class="block secret-cta">Comment</p>
    <p class="block secret-keyword">SKINNY</p>
    <p class="block secret-tail">to get the exact plan.</p>
    <p class="handle" style="top: 397px;">@KBHarlowOnline</p>
  </section>

</body>
</html>
```